Association qui souhaite améliorer l'accès aux personnes en situation de handicap

Nous sommes une association qui a pour objectif d'améliorer l'accessibilité, augmenter l'offre des activités réalisables dans notre région touristique.
Nous souhaitons réaliser un site internet afin de pouvoir communiquer sur notre association. Nous avons déjà conçu notre flyer sur Plumotrix. Nous souhaiterions une base graphique se rapportant à celui-ci. C'est possible de tout retravailler mais nous souhaitons tout de même retrouver la charte graphique ou code couleur du flyer.
Il nous faudrait quelques pages:
- 1 page : Acceuil / Présentation (Home), Il y aurait le descriptif de l'association, avec ses objectifs à +/- moyen terme
- 1 page : Nos réalisations, celle-ci présenterait les éléments que nous avons réalisés avec des zones de textes et des images classées chronologiquement au fur et à mesure des nouveautés
- 1 page : Media, comme la précédente, mais ou on pourrait voir ou lire sur les divers médias qui parlent de nous
- 1 page : Evenements : c'est une page pour présenter divers activités que nous allons organiser
- 1 page : Contact qui indique comment nous contacter et avec la présentation des 5 ou 6 membres du comité
- 1 link donate : qui arrive sur un formulaire de donnée que l'on pourra faire évoluer sur un système de payement par la suite. Cette bannière doit se retrouver sur toutes les pages
Il est nécessaire que se design puisse être transféré sur une lecture sur téléphone mobile
Personnes en situation de handicap
Associatif

```html
<!DOCTYPE html>
<html lang="en">
<head>
<meta charset="utf-8">
<title>Pathway Collective</title>
<link href="https://fonts.googleapis.com/css2?family=Bebas+Neue&family=Raleway:wght@500;600;700;800&family=Nunito+Sans:wght@400;600;700&display=swap" rel="stylesheet">
<style>
:root{
  --red:#be1622;
  --ink:#1d1d1f;
  --body:#3a3a3a;
  --muted:#5c5c5c;
  --white:#ffffff;
  --paper:#fbfbf7;
  --dark:#231f20;
  --event-bg:#3a3a3a;
}
*{margin:0;padding:0;box-sizing:border-box}
html,body{width:1200px;height:3333px;overflow:hidden}
body{position:relative;background:var(--white);font-family:"Nunito Sans",Arial,sans-serif;color:var(--body)}
.abs{position:absolute}
.display{font-family:"Bebas Neue",Impact,sans-serif;letter-spacing:.5px}
.heading{font-family:"Raleway",Arial,sans-serif;font-weight:600;color:var(--ink)}
.accent{color:var(--red)}
.btn{position:absolute;background:var(--red);color:var(--white);border-radius:22px;font-family:"Nunito Sans",Arial,sans-serif;font-weight:700;font-size:12px;display:flex;align-items:center;justify-content:center;letter-spacing:.3px}
.photo{position:absolute}

/* top bar */
.top-bar{left:0;top:0;width:1200px;height:28px;background:var(--red)}
.top-bar .social{position:absolute;top:8px;width:11px;height:11px;border:1.5px solid var(--white);border-radius:2px}
.top-bar .phone{position:absolute;right:130px;top:7px;color:var(--white);font-size:11px;display:flex;align-items:center;gap:4px}

/* nav */
.site-nav{left:0;top:28px;width:1200px;height:62px;background:var(--white)}
.brand{position:absolute;display:flex;align-items:center;gap:8px;font-family:"Raleway",Arial,sans-serif;font-weight:800;color:var(--ink)}
.brand .mark{background:var(--red)}
.nav-link{position:absolute;top:26px;font-size:11.5px;color:var(--ink)}
.nav-link.active{color:var(--red)}

/* hero */
.hero-text p{font-size:13.5px;line-height:19px;color:var(--ink)}

/* sections */
.body-text{font-size:13.5px;line-height:19.5px;color:var(--body)}
.media-card .label{position:absolute;background:var(--white);box-shadow:0 2px 8px rgba(0,0,0,.12);font-size:13px;color:var(--ink);display:flex;align-items:center;justify-content:center;gap:8px}
.event-card{position:absolute;background:var(--white);width:300px;height:370px;top:2095px}
.event-card .date{position:absolute;left:14px;top:13px;width:36px;height:40px;background:var(--red);color:var(--white);font-size:9px;line-height:11px;text-align:center;padding-top:8px}
.event-card h3{position:absolute;left:22px;top:226px;font-family:"Raleway",Arial,sans-serif;font-weight:600;font-size:16px;color:var(--ink)}
.event-card p{position:absolute;left:22px;top:264px;width:260px;font-size:13px;line-height:19px;color:var(--muted)}
.field{position:absolute;border:1px solid #8a8a8a;background:var(--white);font-size:10px;color:#555;padding:8px 9px}

/* footer */
.footer-title{position:absolute;top:3036px;font-family:"Bebas Neue",Impact,sans-serif;font-size:19px;color:var(--red);letter-spacing:.5px}
.footer-list{position:absolute;top:3068px;list-style:none;font-size:11px;line-height:22.5px;color:var(--white)}
.contact-row{position:absolute;left:876px;display:flex;align-items:center;gap:9px;font-size:11px;color:var(--white)}
.contact-row .ring{width:22px;height:22px;border:1.5px solid var(--white);border-radius:50%;display:flex;align-items:center;justify-content:center}
.round-social{position:absolute;top:3174px;width:21px;height:21px;border-radius:50%;background:var(--red)}
</style>
</head>
<body>

<!-- top bar -->
<div class="abs top-bar">
  <span class="social" style="left:130px"></span>
  <span class="social" style="left:151px;border-radius:50%"></span>
  <div class="phone">
    <svg width="10" height="10" viewBox="0 0 24 24"><path fill="#fff" d="M6.6 10.8a15 15 0 0 0 6.6 6.6l2.2-2.2c.3-.3.7-.4 1-.2 1.1.4 2.3.6 3.6.6.6 0 1 .4 1 1V20c0 .6-.4 1-1 1A17 17 0 0 1 3 4c0-.6.4-1 1-1h3.5c.6 0 1 .4 1 1 0 1.3.2 2.5.6 3.6.1.3 0 .7-.2 1z"/></svg>
    +2 (555) 240 7310
  </div>
</div>

<!-- navigation -->
<nav class="abs site-nav">
  <div class="brand" style="left:130px;top:16px;font-size:13px;line-height:14px">
    <span class="mark" style="width:26px;height:26px"></span>
    <span>PATHWAY<br>COLLECTIVE</span>
  </div>
  <span class="nav-link active" style="left:539px">Home</span>
  <svg class="abs" style="left:539px;top:44px" width="30" height="7" viewBox="0 0 30 7"><polyline points="0,1 7,6 14,1 21,6 28,1" fill="none" stroke="#be1622" stroke-width="1.5"/></svg>
  <span class="nav-link" style="left:609px">Our Achievements</span>
  <span class="nav-link" style="left:741px">Media</span>
  <span class="nav-link" style="left:812px">Events</span>
  <span class="nav-link" style="left:886px">Contacts</span>
  <span class="btn" style="left:977px;top:17px;width:93px;height:30px;font-size:11.5px">DONATE</span>
</nav>

<!-- hero -->
<section class="hero">
  <div class="photo" role="img" aria-label="Two smiling women in wheelchairs on a plaza in front of a glass dome" style="left:0;top:90px;width:1200px;height:443px;background:linear-gradient(90deg,#f1e6f0 0%,#ece1ee 40%,#d9cfdc 60%,#b9a9b4 80%,#cfc5d2 100%)"></div>
  <div class="abs hero-text" style="left:130px;top:210px;width:440px">
    <div class="display" style="font-size:31px;color:var(--ink);line-height:30px">ACCESS THE</div>
    <div style="font-family:'Raleway',Arial,sans-serif;font-weight:800;font-size:44px;line-height:50px;color:var(--ink);letter-spacing:.5px">TOURIST <span class="accent">REGION</span></div>
    <p style="margin-top:16px">The resources of the association come from subscriptions, donations and events organized throughout the year.</p>
  </div>
  <span class="btn" style="left:130px;top:369px;width:117px;height:39px">READ MORE</span>
</section>

<!-- welcome -->
<section class="welcome">
  <div class="photo" role="img" aria-label="Man with a white cane walking down steps between columns in a garden" style="left:130px;top:600px;width:460px;height:365px;border-radius:3px;background:linear-gradient(90deg,#6f8a3e,#c9b99a 45%,#5b7a2e)"></div>
  <div class="display abs" style="left:611px;top:636px;font-size:21px;color:var(--ink)">WELCOME TO</div>
  <h2 class="heading abs" style="left:611px;top:666px;font-size:35px;font-weight:500">Pathway <span class="accent">Collective</span></h2>
  <p class="body-text abs" style="left:611px;top:727px;width:460px">Sed ut perspiciatis unde omnis iste natus error sit voluptatem accusantium doloremque laudantium, totam rem aperiam, eaque ipsa quae ab illo inventore veritatis et quasi architecto beatae vitae dicta sunt explicabo. Nemo enim ipsam voluptatem quia voluptas sit aspernatur aut odit aut fugit, sed quia consequuntur magni dolores eos qui ratione voluptatem sequi nesciunt.</p>
  <span class="btn" style="left:611px;top:870px;width:117px;height:39px">READ MORE</span>
</section>

<!-- achievements -->
<section class="achievements">
  <div class="photo" role="img" aria-label="Person in a wheelchair and a companion looking over a mountain meadow" style="left:0;top:1031px;width:1200px;height:515px;background:linear-gradient(90deg,#2c2f2a,#3c4238 55%,#2a2d29)"></div>
  <svg class="abs" style="left:0;top:1031px" width="1200" height="515" viewBox="0 0 1200 515" role="img" aria-label="Close-up of a hand touching tall grass beside a wheelchair wheel">
    <defs><linearGradient id="grass" x1="0" y1="0" x2="1" y2="0"><stop offset="0" stop-color="#6e8a46"/><stop offset=".6" stop-color="#9aa86a"/><stop offset="1" stop-color="#3e3a3a"/></linearGradient></defs>
    <polygon points="729,0 1200,0 1200,515 1055,515 598,263" fill="url(#grass)"/>
    <polyline points="729,0 598,263 1055,515" fill="none" stroke="#fff" stroke-width="6"/>
  </svg>
  <h2 class="heading abs" style="left:132px;top:1158px;font-size:33px;color:var(--white);font-weight:500">Our Achievements</h2>
  <p class="body-text abs" style="left:132px;top:1224px;width:460px;color:var(--white)">Sed ut perspiciatis unde omnis iste natus error sit voluptatem accusantium doloremque laudantium, totam rem aperiam, eaque ipsa quae ab illo inventore veritatis et quasi architecto beatae vitae dicta sunt explicabo. Nemo enim ipsam voluptatem quia voluptas sit aspernatur aut odit aut fugit, sed quia consequuntur magni dolores eos qui ratione voluptatem sequi nesciunt.</p>
  <span class="btn" style="left:132px;top:1373px;width:117px;height:39px">READ MORE</span>
</section>

<!-- media -->
<section class="media">
  <h2 class="heading abs" style="left:0;width:1200px;text-align:center;top:1603px;font-size:33px;font-weight:500">Our Media</h2>
  <p class="abs" style="left:0;width:1200px;text-align:center;top:1651px;font-size:13px;color:var(--body)">Sed ut perspiciatis unde omnis iste natus error sit voluptatem</p>

  <div class="media-card">
    <div class="photo" role="img" aria-label="Caregiver holding hands with an elderly woman in a garden chair" style="left:130px;top:1699px;width:300px;height:180px;background:linear-gradient(135deg,#5f7f3c,#b9c7a0 60%,#dde2d6)"></div>
    <div class="label" style="left:157px;top:1860px;width:247px;height:40px">Voluptas Sit Aspernatur <span class="accent" style="font-weight:700;font-size:15px">+</span></div>
  </div>
  <div class="media-card">
    <div class="photo" role="img" aria-label="Two people helping a seated woman in the snow" style="left:449px;top:1699px;width:300px;height:180px;background:linear-gradient(135deg,#c8cdd2,#eef1f3 55%,#8b8f93)"></div>
    <div class="label" style="left:476px;top:1860px;width:247px;height:40px">Voluptas Sit Aspernatur <span class="accent" style="font-weight:700;font-size:15px">+</span></div>
  </div>
  <div class="media-card">
    <div class="photo" role="img" aria-label="Doctor examining a seated patient in a clinic room" style="left:770px;top:1699px;width:300px;height:180px;background:linear-gradient(135deg,#d9cfa8,#efe9d2 55%,#8e8a78)"></div>
    <div class="label" style="left:797px;top:1860px;width:247px;height:40px">Voluptas Sit Aspernatur <span class="accent" style="font-weight:700;font-size:15px">+</span></div>
  </div>
</section>

<!-- events -->
<section class="events">
  <div class="photo" role="img" aria-label="Greyscale background of a cyclist with adapted bikes on a street" style="left:0;top:1967px;width:1200px;height:567px;background:linear-gradient(180deg,#4a4a4a,#333 60%,#2a2a2a)"></div>
  <h2 class="heading abs" style="left:0;width:1200px;text-align:center;top:2030px;font-size:33px;color:var(--white);font-weight:500">Recent Event</h2>

  <article class="event-card" style="left:130px">
    <div role="img" aria-label="Young girl blowing a dandelion on a lawn" style="width:300px;height:207px;background:linear-gradient(135deg,#4d8a2a,#7db34a 60%,#3a5fa0)"></div>
    <div class="date">12<br>MAY</div>
    <h3>Neque Porro Wuisquam</h3>
    <p>Sed ut perspiciatis unde omnis iste natus error sit voluptatem accusantium</p>
    <span class="btn" style="left:24px;top:312px;width:117px;height:39px">READ MORE</span>
  </article>
  <article class="event-card" style="left:449px">
    <div role="img" aria-label="Group of wheelchair users gathered under a lit terrace at night" style="width:300px;height:207px;background:linear-gradient(135deg,#2b2f2b,#8d958a 55%,#3e443c)"></div>
    <div class="date">12<br>MAY</div>
    <h3>Neque Porro Wuisquam</h3>
    <p>Sed ut perspiciatis unde omnis iste natus error sit voluptatem accusantium</p>
    <span class="btn" style="left:24px;top:312px;width:117px;height:39px">READ MORE</span>
  </article>
  <article class="event-card" style="left:770px">
    <div role="img" aria-label="Team of young wheelchair athletes in red and blue jerseys on a court" style="width:300px;height:207px;background:linear-gradient(135deg,#6f7a80,#a7a9a2 50%,#4e6a3b)"></div>
    <div class="date">12<br>MAY</div>
    <h3>Neque Porro Wuisquam</h3>
    <p>Sed ut perspiciatis unde omnis iste natus error sit voluptatem accusantium</p>
    <span class="btn" style="left:24px;top:312px;width:117px;height:39px">READ MORE</span>
  </article>
</section>

<!-- contact -->
<section class="contact">
  <div class="abs" style="left:0;top:2534px;width:1200px;height:460px;background:var(--paper)"></div>
  <div class="photo" role="img" aria-label="Man riding an adapted cycle on a grassy hillside" style="left:130px;top:2602px;width:421px;height:317px;background:linear-gradient(135deg,#b9c1b6,#8fa66a 45%,#7a2a30 70%,#5a5e60)"></div>
  <h2 class="heading abs" style="left:608px;top:2640px;font-size:33px;font-weight:500">Contact Us</h2>
  <p class="abs" style="left:609px;top:2688px;font-size:13px;color:var(--ink)">Sed ut perspiciatis unde omnis iste natus error</p>
  <div class="field" style="left:609px;top:2742px;width:227px;height:34px">Name:</div>
  <div class="field" style="left:609px;top:2790px;width:227px;height:34px">Email:</div>
  <div class="field" style="left:609px;top:2837px;width:227px;height:34px">Phone:</div>
  <div class="field" style="left:842px;top:2742px;width:228px;height:82px">Comments:</div>
  <div class="abs" style="left:842px;top:2837px;width:228px;height:34px;background:var(--red);color:var(--white);font-size:10.5px;display:flex;align-items:center;justify-content:center">SUBMIT</div>
</section>

<!-- footer -->
<footer>
  <svg class="abs" style="left:0;top:2873px" width="1200" height="460" viewBox="0 0 1200 460"><polygon points="0,52 472,127 1200,0 1200,460 0,460" fill="#231f20"/></svg>
  <div class="brand" style="left:130px;top:3046px;font-size:15px;line-height:16px;color:var(--white)">
    <span class="mark" style="width:34px;height:34px"></span>
    <span>PATHWAY<br>COLLECTIVE</span>
  </div>
  <p class="abs" style="left:130px;top:3105px;width:205px;font-size:10.5px;line-height:16px;color:var(--white)">Sed ut perspiciatis unde omnis iste natus error sit voluptatem accusantium rem aperiam</p>
  <span class="round-social" style="left:130px"></span>
  <span class="round-social" style="left:165px"></span>

  <div class="footer-title" style="left:450px">SITEMAP</div>
  <ul class="footer-list" style="left:450px"><li>Home</li><li>Our Achivements</li><li>Media</li><li>Events</li><li>Contact Us</li></ul>

  <div class="footer-title" style="left:669px">OTHERS</div>
  <ul class="footer-list" style="left:669px"><li>Privacy Policy</li><li>Terms &amp; Conditions</li><li>Leagal</li><li>Donate</li><li>Help / Support</li></ul>

  <div class="footer-title" style="left:876px">CONTACTS</div>
  <div class="contact-row" style="top:3069px">
    <span class="ring"><svg width="10" height="12" viewBox="0 0 24 28"><path fill="#be1622" d="M12 0a9 9 0 0 0-9 9c0 7 9 19 9 19s9-12 9-19a9 9 0 0 0-9-9zm0 12a3 3 0 1 1 0-6 3 3 0 0 1 0 6z"/></svg></span>
    <span style="margin-top:-6px">Marlow Lane 4420 Val Serene</span>
  </div>
  <div class="contact-row" style="top:3109px">
    <span class="ring"><svg width="10" height="10" viewBox="0 0 24 24"><path fill="#be1622" d="M6.6 10.8a15 15 0 0 0 6.6 6.6l2.2-2.2c.3-.3.7-.4 1-.2 1.1.4 2.3.6 3.6.6.6 0 1 .4 1 1V20c0 .6-.4 1-1 1A17 17 0 0 1 3 4c0-.6.4-1 1-1h3.5c.6 0 1 .4 1 1 0 1.3.2 2.5.6 3.6.1.3 0 .7-.2 1z"/></svg></span>
    <span style="margin-top:-6px">+2 (555) 240 7310</span>
  </div>
  <div class="contact-row" style="top:3152px">
    <span class="ring"><svg width="11" height="9" viewBox="0 0 24 18"><rect x="1" y="1" width="22" height="16" rx="2" fill="#be1622"/><polyline points="2,3 12,10 22,3" fill="none" stroke="#231f20" stroke-width="2"/></svg></span>
    <span style="margin-top:-6px">info@pathwaycollective.org</span>
  </div>

  <p class="abs" style="left:0;width:1200px;text-align:center;top:3267px;font-size:10.5px;color:var(--white)">Copyright © 2022 <span class="accent">Pathway Collective</span>. All Rights Reserved.</p>
</footer>

</body>
</html>
```